NimbaVault Website Homepage Design

Please provide your idea of homepage for a hosting company. This project is for DESIGN only, no coding.

It must use/combine colors used in logo, clean, modern look.

Homepage must consist of at least 4 sections (example: testimonials, services, and so on. not necesarily all of them). We would like the navigation to be horizontal, but not mandatory.

You can include a preview of services page (optional, not a must).

Number of Pages Required

1 page

Font styles to use
Sans Serif

```html
<!DOCTYPE html>
<html lang="en">
<head>
<meta charset="utf-8">
<title>NimbaVault – Homepage</title>
<link rel="stylesheet" href="https://fonts.googleapis.com/css2?family=Montserrat:wght@300;400;500;600;700;800&family=Roboto:wght@400;500;700&display=swap">
<style>
:root{
  --blue:#1689d4;
  --blue-deep:#0f6fb0;
  --black:#000;
  --ink:#111;
  --grey:#6d6d6d;
  --light:#cfcfcf;
  --white:#fff;
  --navy:#0b1a33;
}
*{margin:0;padding:0;box-sizing:border-box}
html,body{width:1200px;height:3000px;overflow:hidden;background:var(--white)}
body{font-family:"Montserrat",sans-serif;color:var(--ink)}
section,header,footer{position:relative;width:1200px;overflow:hidden}
.abs{position:absolute}
.brand{font-family:"Montserrat",sans-serif;font-weight:700;color:var(--blue);letter-spacing:1px}

/* nav */
.site-nav{height:58px;background:var(--black)}
.site-nav .brand{left:125px;top:12px;font-size:28px}
.nav-link{top:19px;font-family:"Roboto",sans-serif;font-weight:700;font-size:14px;color:var(--white)}
.nav-link.active::after{content:"";position:absolute;left:0;right:0;bottom:-11px;height:3px;background:var(--blue)}

/* hero */
.hero{height:536px;background:#0a0d14}
.hero-photo{inset:0;background:radial-gradient(circle at 75% 85%,rgba(230,150,40,.55),transparent 18%),radial-gradient(circle at 42% 52%,rgba(200,140,90,.35),transparent 22%),radial-gradient(circle at 78% 30%,rgba(120,90,80,.6),transparent 30%),linear-gradient(90deg,#07090e 0%,#121a26 45%,#2a2c33 70%,#191c24 100%)}
.hero-kicker{left:125px;top:122px;font-size:42px;font-weight:300;letter-spacing:3px;color:var(--white)}
.hero-title{left:125px;top:170px;font-size:43px;font-weight:800;letter-spacing:1.5px;color:var(--white)}
.hero-title.blue{top:222px;color:var(--blue)}
.hero-btn{left:125px;top:318px;width:200px;height:46px;border:2.5px solid var(--blue);color:var(--white);font-size:19px;font-weight:500;display:flex;align-items:center;justify-content:center}
.hero-arrow{top:210px}

/* split sections */
.split{background:var(--white)}
.about{height:498px}
.why{height:464px}
.eyebrow{left:125px;top:74px;font-size:28px;font-weight:500;letter-spacing:2px;color:#6b6b6b}
.split-title{left:125px;font-size:36px;font-weight:700;color:var(--ink)}
.rule{height:4px;width:92px;background:var(--blue)}
.copy{left:125px;width:440px;font-size:15.5px;line-height:20px;color:var(--grey)}

/* services */
.services{height:730px;background:radial-gradient(ellipse at 50% 115%,#2a2a2a 0%,#0b0b0b 45%,#000 70%)}
.section-heading{left:0;right:0;text-align:center;font-family:"Roboto",sans-serif;font-weight:700;font-size:29px;color:var(--white)}
.svc-title{font-family:"Roboto",sans-serif;font-weight:700;font-size:13px;color:var(--white)}
.svc-copy{font-family:"Roboto",sans-serif;font-size:10.5px;line-height:16px;color:#c8c8c8;width:270px;margin-top:6px}

/* testimonials */
.testimonials{height:354px;background:linear-gradient(100deg,#2a88cf 0%,#1a86d2 40%,#3c95d8 75%,#1877bf 100%)}
.testimonials .section-heading{font-family:"Montserrat",sans-serif;font-weight:600;color:var(--navy);letter-spacing:2px;top:28px}
.quote-card{left:319px;top:103px;width:715px;height:208px;background:var(--white);box-shadow:0 4px 14px rgba(0,0,0,.15)}
.avatar{left:170px;top:111px;width:190px;height:190px;border-radius:50%;background:radial-gradient(circle at 50% 45%,#e7dfd6,#c8bcae 70%);border:5px solid #e8eef4}
.quote-text{left:133px;top:36px;width:520px;font-size:16px;line-height:20px;color:#1a1a1a}
.quote-author{left:133px;top:153px;font-size:16px;color:#1a1a1a}

/* footer */
.site-footer{height:360px;background:var(--black);color:var(--white)}
.site-footer .brand{left:125px;top:62px;font-size:34px}
.footer-about{left:125px;top:130px;width:330px;font-size:13.5px;line-height:16px}
.footer-head{font-size:13.5px;font-weight:700}
.footer-item{font-size:13.5px;color:#e4e4e4}
.social{width:44px;height:44px;border-radius:50%;background:var(--white);top:245px;display:flex;align-items:center;justify-content:center}
.social span{width:16px;height:16px;border-radius:3px;background:var(--blue)}
.footer-rule{left:125px;top:310px;width:948px;height:1px;background:#444}
.copyright{top:328px;left:0;right:0;text-align:center;font-size:10px;color:#555}
</style>
</head>
<body>

<header class="site-nav">
  <div class="abs brand">NimbaVault</div>
  <a class="abs nav-link active" style="left:462px">Home</a>
  <a class="abs nav-link" style="left:572px">About Us</a>
  <a class="abs nav-link" style="left:707px">Our Services</a>
  <a class="abs nav-link" style="left:869px">Testimonial</a>
  <a class="abs nav-link" style="left:1023px">Contact Us</a>
</header>

<section class="hero">
  <div class="abs hero-photo" role="img" aria-label="Photo of a woman using a tablet by a window with city lights at night"></div>
  <div class="abs hero-kicker">INFORMATION</div>
  <div class="abs hero-title">HOSTING</div>
  <div class="abs hero-title blue">DATA SERVICE</div>
  <div class="abs hero-btn">Learn More</div>
  <svg class="abs hero-arrow" style="left:32px" width="24" height="40" viewBox="0 0 24 40"><path d="M18 4 L5 20 L18 36" fill="none" stroke="var(--blue)" stroke-width="3.5"/></svg>
  <svg class="abs hero-arrow" style="left:1145px" width="24" height="40" viewBox="0 0 24 40"><path d="M6 4 L19 20 L6 36" fill="none" stroke="var(--blue)" stroke-width="3.5"/></svg>
</section>

<section class="split about">
  <svg class="abs" style="left:0;top:0" width="1200" height="498" viewBox="0 0 1200 498">
    <polygon points="800,0 1200,0 1200,435 1035,435" fill="#c9ccd0" role="img" aria-label="Photo of two businessmen in suits at a meeting table"/>
    <polygon points="787,0 1035,435 540,435" fill="var(--black)"/>
    <polygon points="787,35 963,387 618,387" fill="var(--white)"/>
    <polygon points="787,178 959,435 622,435" fill="var(--blue)"/>
  </svg>
  <div class="abs eyebrow">WHO WE ARE</div>
  <div class="abs split-title" style="top:116px">ABOUT HOSTING</div>
  <div class="abs rule" style="left:125px;top:166px"></div>
  <p class="abs copy" style="top:203px">lorem ipsum dolor sit amet, consectetur adipiscing elit, sed do eiusmod tempor incididunt ut labore et dolore magna aliqua. ut enim ad minim veniam quis nostrud exercitation ullamco laboris nisi</p>
  <p class="abs copy" style="top:293px">lorem ipsum dolor sit amet, consectetur adipiscing elit, sed do eiusmod tempor incididunt ut labore et dolore magna aliqua. ut enim ad minim veniam</p>
</section>

<section class="services">
  <div class="abs section-heading" style="top:38px">OUR SERVICES</div>
  <div class="abs rule" style="left:686px;top:75px;width:66px;height:3px"></div>
  <svg class="abs" style="left:0;top:0" width="1200" height="730" viewBox="0 0 1200 730">
    <g fill="none" stroke="var(--blue)" stroke-width="8">
      <circle cx="341" cy="385" r="178"/>
      <path d="M341 207 V145 A257 240 0 0 1 341 625 V563"/>
    </g>
    <g fill="none" stroke="var(--white)" stroke-width="2.5">
      <polyline points="488,188 510,166 563,166"/>
      <polyline points="574,284 595,240 653,240"/>
      <polyline points="598,385 718,385"/>
      <polyline points="574,486 595,532 653,532"/>
      <polyline points="488,582 510,619 567,619"/>
    </g>
    <g fill="#8fb3d6" stroke="var(--blue)" stroke-width="3">
      <circle cx="488" cy="188" r="9"/><circle cx="574" cy="284" r="9"/><circle cx="598" cy="385" r="9"/><circle cx="574" cy="486" r="9"/><circle cx="488" cy="582" r="9"/>
    </g>
    <g fill="var(--white)">
      <circle cx="563" cy="166" r="6"/><circle cx="653" cy="240" r="6"/><circle cx="718" cy="385" r="6"/><circle cx="653" cy="532" r="6"/><circle cx="567" cy="619" r="6"/>
    </g>
    <g fill="var(--blue)">
      <circle cx="619" cy="169" r="33"/><circle cx="715" cy="239" r="33"/><circle cx="767" cy="385" r="33"/><circle cx="715" cy="532" r="33"/><circle cx="619" cy="619" r="33"/>
    </g>
    <g fill="none" stroke="var(--white)" stroke-width="2">
      <circle cx="611" cy="176" r="5"/><circle cx="627" cy="176" r="5"/><path d="M603 165 H635 M609 165 Q619 150 629 165"/>
      <circle cx="715" cy="239" r="16"/><path d="M699 239 H731 M715 223 V255"/>
      <rect x="754" y="372" width="12" height="9"/><rect x="770" y="389" width="12" height="9"/><path d="M760 381 V393 H770"/>
      <rect x="700" y="520" width="30" height="20"/><path d="M707 533 L714 526 L721 531 L726 524 M710 546 H720"/>
      <rect x="603" y="604" width="32" height="30" rx="4"/><path d="M607 628 L616 617 L622 624 L627 619 L632 628"/>
    </g>
  </svg>
  <div class="abs brand" style="left:241px;top:366px;font-size:32px;width:200px;text-align:center">NimbaVault</div>

  <div class="abs" style="left:681px;top:124px"><div class="svc-title">PRIVATE NETWORKING</div><p class="svc-copy">Lorem ipsum dolor sit amet, consectetur adipiscing elit sed do eiusmod tempor incididunt ut labore et</p></div>
  <div class="abs" style="left:781px;top:211px"><div class="svc-title">CYBER REGISTRY</div><p class="svc-copy">Lorem ipsum dolor sit amet, consectetur adipiscing elit sed do eiusmod tempor incididunt ut labore et</p></div>
  <div class="abs" style="left:819px;top:356px"><div class="svc-title">INFRA BLUEPRINT PROVIDER</div><p class="svc-copy">Lorem ipsum dolor sit amet, consectetur adipiscing elit sed do eiusmod tempor incididunt ut labore et</p></div>
  <div class="abs" style="left:781px;top:506px"><div class="svc-title">NATIVELY INTEGRATED</div><p class="svc-copy">Lorem ipsum dolor sit amet, consectetur adipiscing elit sed do eiusmod tempor incididunt ut labore et</p></div>
  <div class="abs" style="left:689px;top:600px"><div class="svc-title">CUSTOM IMAGES</div><p class="svc-copy">Lorem ipsum dolor sit amet, consectetur adipiscing elit sed do eiusmod tempor incididunt ut labore et</p></div>
</section>

<section class="split why">
  <svg class="abs" style="left:0;top:0" width="1200" height="464" viewBox="0 0 1200 464">
    <rect x="0" y="414" width="760" height="50" fill="var(--black)"/>
    <polygon points="797,0 1200,0 1200,464 1046,464" fill="#1f2a36" role="img" aria-label="Photo of business colleagues looking at a tablet"/>
    <polygon points="760,0 1031,464 523,464" fill="var(--black)"/>
    <polygon points="757,37 948,464 580,464" fill="var(--white)"/>
    <polygon points="760,190 943,464 587,464" fill="var(--blue)"/>
    <line x1="797" y1="0" x2="1046" y2="464" stroke="var(--white)" stroke-width="3"/>
  </svg>
  <div class="abs split-title" style="top:86px">WHY <span style="color:var(--blue)">NimbaVault</span>?</div>
  <div class="abs rule" style="left:125px;top:137px"></div>
  <p class="abs copy" style="top:180px">lorem ipsum dolor sit amet, consectetur adipiscing elit, sed do eiusmod tempor incididunt ut labore et dolore magna aliqua. ut enim ad minim veniam quis nostrud exercitation ullamco laboris nisi</p>
  <p class="abs copy" style="top:271px">lorem ipsum dolor sit amet, consectetur adipiscing elit, sed do eiusmod tempor incididunt ut labore et dolore magna aliqua. ut enim ad minim veniam</p>
</section>

<section class="testimonials">
  <div class="abs section-heading">TESTIMONIALS</div>
  <div class="abs" style="left:474px;top:71px;width:251px;height:3px;background:var(--navy)"></div>
  <div class="abs quote-card">
    <svg class="abs" style="left:70px;top:28px" width="40" height="150" viewBox="0 0 40 150">
      <path d="M4 4 h12 v12 h-6 q0 6 6 8 v4 q-12 -2 -12 -14z M22 4 h12 v12 h-6 q0 6 6 8 v4 q-12 -2 -12 -14z" fill="#9a9a9a"/>
      <line x1="21" y1="40" x2="21" y2="145" stroke="#555" stroke-width="1.5"/>
    </svg>
    <p class="abs quote-text">Lorem Ipsum Dolor Sit Amet, Consectetur Adipiscing Elit, Sed Do Eiusmod Tempor Incididunt Ut Labore Et Dolore Magna Aliqua. Ut Enim Ad Minim Veniam, Quis Nostrud Exercitation Ullamco Laboris Nisi Ut Aliquip Ex Ea Commodo Consequat. Duis Aute Irure Dolor In</p>
    <div class="abs quote-author">Marlo Fenwick -Brightstack Drives</div>
    <svg class="abs" style="left:453px;top:150px" width="36" height="30" viewBox="0 0 36 30">
      <path d="M32 26 h-12 v-12 h6 q0 -6 -6 -8 v-4 q12 2 12 14z M14 26 h-12 v-12 h6 q0 -6 -6 -8 v-4 q12 2 12 14z" fill="#9a9a9a"/>
    </svg>
  </div>
  <div class="abs avatar" role="img" aria-label="Portrait photo of the client giving the testimonial"></div>
</section>

<footer class="site-footer">
  <div class="abs brand">NimbaVault</div>
  <p class="abs footer-about">Lorem Ipsum Dolor Sit Amet,Consectetur Adipiscing Elit, Sed Do Eiusmod Tempor Incididunt Ut Labore Et Dolore Magn A Aliqua. Ut Enim Ad Minim Veniam,</p>
  <div class="abs footer-head" style="left:125px;top:218px">Follow Us</div>
  <div class="abs social" style="left:120px"><span></span></div>
  <div class="abs social" style="left:182px"><span></span></div>
  <div class="abs social" style="left:244px"><span></span></div>

  <div class="abs footer-head" style="left:628px;top:82px">Home</div>
  <div class="abs footer-item" style="left:628px;top:125px">Home</div>
  <div class="abs footer-item" style="left:628px;top:169px">Services</div>
  <div class="abs footer-item" style="left:628px;top:213px">About Us</div>
  <div class="abs footer-item" style="left:628px;top:256px">Join</div>

  <div class="abs footer-head" style="left:752px;top:82px">Quick Links</div>
  <div class="abs footer-item" style="left:752px;top:125px">Loremipsum</div>
  <div class="abs footer-item" style="left:752px;top:169px">Loremipsum</div>
  <div class="abs footer-item" style="left:752px;top:213px">Loremipsum</div>
  <div class="abs footer-item" style="left:752px;top:256px">Loremipsum</div>

  <div class="abs footer-head" style="left:934px;top:82px">Contact Us</div>
  <div class="abs footer-item" style="left:934px;top:125px">#555-014-288</div>
  <div class="abs footer-item" style="left:934px;top:169px">Hi@NimbaVault.Example</div>

  <div class="abs footer-rule"></div>
  <div class="abs copyright">Copyright 2021 NimbaVault &nbsp;|&nbsp; All Right Reserved</div>
</footer>

</body>
</html>
```